MRT Property - Business Cards

Looking for a business card & general letterhead, signage etc design for our new logo.

Colours:
000a20
0056a2
00b5ef
0088ce
68cef2

Fonts:
Poppins
Karla

Please keep look and feel of new brand - example in the zip package I sent.

```html
<!DOCTYPE html>
<html lang="en">
<head>
<meta charset="utf-8">
<title>MRT Property – Business Cards</title>
<link rel="stylesheet" href="https://fonts.googleapis.com/css2?family=Montserrat:wght@400;500;700&family=Gochi+Hand&display=swap">
<style>
  :root {
    --ink: #000a20;
    --brand-navy: #0056a2;
    --brand-cyan: #00b5ef;
    --brand-mid: #0088ce;
    --brand-sky: #68cef2;
    --card-back: #0b55a3;
    --text: #1f1f1f;
    --paper: #ffffff;
    --stage: #9a9a9a;
  }
  * { box-sizing: border-box; margin: 0; padding: 0; }
  html, body { width: 1093px; height: 1200px; overflow: hidden; }
  body {
    position: relative;
    background: var(--stage);
    font-family: "Montserrat", Arial, sans-serif;
    color: var(--text);
  }
  .card {
    position: absolute;
    left: 265px;
    width: 580px;
    border-radius: 18px;
    overflow: hidden;
  }
  .card--front { top: 225px; height: 363px; background: var(--paper); }
  .card--back  { top: 616px; height: 365px; background: var(--card-back); }

  .wordmark { position: absolute; color: var(--brand-navy); font-weight: 700; line-height: 1; }
  .card--front .wordmark { left: 21px; top: 22px; }
  .wordmark__name { display: block; font-size: 84px; letter-spacing: -2px; }
  .wordmark__sub { display: block; font-size: 19px; letter-spacing: 13.5px; margin: 8px 0 0 4px; }

  .holder { position: absolute; right: 34px; top: 29px; text-align: left; }
  .holder__name {
    display: block;
    font-family: "Gochi Hand", cursive;
    font-size: 28px;
    line-height: 1;
    color: var(--brand-navy);
  }
  .holder__title { display: block; font-size: 13px; font-weight: 500; margin-top: 5px; color: var(--text); }
  .accent-bar { position: absolute; right: 0; top: 27px; width: 20px; height: 46px; background: var(--brand-navy); }

  .address { position: absolute; left: 24px; top: 200px; font-size: 14px; line-height: 17px; font-style: normal; }

  .contacts { position: absolute; left: 25px; top: 264px; list-style: none; font-size: 13.5px; }
  .contacts li { display: flex; align-items: center; height: 25px; }
  .contacts svg { width: 14px; height: 14px; margin-right: 9px; fill: var(--brand-mid); }

  .pattern-field {
    position: absolute; inset: 0;
    background:
      linear-gradient(135deg, rgba(0,181,239,0.55) 0%, rgba(0,136,206,0.25) 30%, rgba(30,60,120,0.35) 60%, rgba(30,60,120,0.45) 100%);
  }
  .card--back .wordmark { left: 349px; top: 270px; color: var(--paper); }
  .card--back .wordmark__name { font-size: 33px; letter-spacing: -0.5px; }
  .card--back .wordmark__sub { font-size: 8px; letter-spacing: 4.6px; margin: 3px 0 0 3px; }
  .wordmark__dot { position: absolute; left: -30px; top: 4px; width: 24px; height: 24px; border-radius: 50%; background: var(--brand-sky); }
</style>
</head>
<body>
  <section class="card card--front">
    <div class="wordmark">
      <span class="wordmark__name">MRT</span>
      <span class="wordmark__sub">PROPERTY</span>
    </div>

    <div class="holder">
      <span class="holder__name">Dana Whitfield</span>
      <span class="holder__title">Managing Director</span>
    </div>
    <div class="accent-bar"></div>

    <address class="address">240 Harbor Crest Lane<br>Ridgeford, MS 39204</address>

    <ul class="contacts">
      <li>
        <svg viewBox="0 0 24 24" aria-hidden="true"><path d="M6.6 10.8a15.1 15.1 0 0 0 6.6 6.6l2.2-2.2c.3-.3.7-.4 1-.2 1.1.4 2.3.6 3.6.6.6 0 1 .4 1 1V20c0 .6-.4 1-1 1A17 17 0 0 1 3 4c0-.6.4-1 1-1h3.5c.6 0 1 .4 1 1 0 1.3.2 2.5.6 3.6.1.3 0 .7-.2 1z"/></svg>
        555.314.2760
      </li>
      <li>
        <svg viewBox="0 0 24 24" aria-hidden="true"><path d="M2 5h20v14H2z M2 6l10 7 10-7" /></svg>
        info@mrtproperty.com
      </li>
      <li>
        <svg viewBox="0 0 24 24" aria-hidden="true"><circle cx="12" cy="12" r="10"/></svg>
        www.mrtproperty.com
      </li>
    </ul>
  </section>

  <section class="card card--back">
    <div class="pattern-field" role="img" aria-label="Repeating brand pattern fading from light cyan to deep navy"></div>
    <div class="wordmark">
      <span class="wordmark__dot"></span>
      <span class="wordmark__name">MRT</span>
      <span class="wordmark__sub">PROPERTY</span>
    </div>
  </section>
</body>
</html>
```